BUSINESS CARD - HALLORAN FIELD SERVICES

I would like to create a business card for my fertilizer spreading business. I would like to incorporate my existing logo and also a description of the services offered. The business card will be given to farmers so must be kept simple but effective. It will also be left in stores so much also be eye catching in order to stand out from other cards.

Target Market(s)

FARMERS

Requirements
Must have
• FRONT OF CARD = EXISTING LOGO + "CUSTOMISED SPREADING" below the logo

REAR Of CARD = SERVICES OFFERED AND CONTACT DETAILS

- Bulk fertilizer including Lime, Gypsum, Manure & Compost
- Granular fertilizer including Single Super, Urea, Gran-am, & Custom Blends
- Modern equipment - Autosteer & Variable Rate Capable
- Friendly & Reliable Service
- Contact Gus: 0417 552 308
Nice to have
• utilize same color scheme as existing logo

```html
<!DOCTYPE html>
<html lang="en">
<head>
<meta charset="utf-8">
<title>Halloran Field Services – Business Card</title>
<link href="https://fonts.googleapis.com/css2?family=Open+Sans:wght@400;600;700&display=swap" rel="stylesheet">
<style>
  :root {
    --backdrop: #e4e4e4;
    --card: #f4f4f4;
    --charcoal: #555555;
    --ink: #333333;
    --orange: #ef8f1f;
    --soft-grey: #dcdcdc;
  }
  * { margin: 0; padding: 0; box-sizing: border-box; }
  html, body {
    width: 1200px; height: 960px; overflow: hidden;
    background: var(--backdrop);
    font-family: "Open Sans", Arial, sans-serif;
  }
  .card {
    position: absolute; left: 308px; width: 588px; height: 359px;
    background: var(--card); overflow: hidden;
  }
  .card--front { top: 100px; }
  .card--back { top: 505px; }

  /* Front */
  .brand-dot {
    position: absolute; left: 244px; top: 80px;
    width: 100px; height: 100px; border-radius: 50%;
    background: var(--charcoal);
  }
  .brand-name {
    position: absolute; left: 0; right: 0; top: 222px;
    text-align: center; font-weight: 700; font-size: 31px;
    color: var(--charcoal); letter-spacing: 0.5px;
  }
  .brand-rule {
    position: absolute; left: 126px; width: 336px; top: 277px;
    height: 2px; background: var(--orange);
  }
  .front-tagline {
    position: absolute; left: 0; right: 0; top: 312px;
    text-align: center; font-weight: 700; font-size: 15px;
    letter-spacing: 1.2px; color: var(--charcoal);
  }

  /* Back */
  .back-disc {
    position: absolute; left: -100px; top: 40px;
    width: 390px; height: 390px; border-radius: 50%;
    background: var(--soft-grey);
  }
  .contact {
    position: absolute; left: 64px; top: 88px; text-align: center;
  }
  .contact__name {
    font-weight: 700; font-size: 27px; color: var(--orange);
    letter-spacing: 1px; line-height: 1.1;
  }
  .contact__phone {
    display: flex; align-items: center; gap: 5px;
    font-size: 17px; font-weight: 600; color: var(--ink); margin-top: 4px;
  }
  .back-brand {
    position: absolute; left: 18px; top: 270px; width: 230px;
    font-weight: 700; font-size: 17px; color: var(--charcoal);
    text-align: center; line-height: 1.3;
  }
  .services {
    position: absolute; left: 330px; top: 55px; list-style: none;
    font-size: 15px; color: var(--ink); line-height: 19.5px;
  }
  .services li { position: relative; padding-left: 16px; margin-bottom: 10px; }
  .services li svg { position: absolute; left: 0; top: 5px; }
  .services strong { font-weight: 700; display: block; }
</style>
</head>
<body>
  <section class="card card--front" aria-label="Card front">
    <div class="brand-dot"></div>
    <div class="brand-name">HALLORAN FIELD SERVICES</div>
    <div class="brand-rule"></div>
    <div class="front-tagline">CUSTOMISED SPREADING</div>
  </section>

  <section class="card card--back" aria-label="Card back">
    <div class="back-disc"></div>
    <div class="contact">
      <div class="contact__name">GUS</div>
      <div class="contact__phone">
        <svg width="18" height="18" viewBox="0 0 18 18" aria-hidden="true">
          <circle cx="9" cy="9" r="8" fill="none" stroke="#ef8f1f" stroke-width="1.6"/>
          <path d="M6 5.2c.5-.4 1-.3 1.3.2l.7 1.2c.2.4.1.8-.2 1l-.5.4c.4 1 1.1 1.7 2.1 2.1l.4-.5c.3-.3.7-.4 1-.2l1.2.7c.5.3.6.8.2 1.3-.6.8-1.5 1-2.4.6C7.9 11.3 6.7 10.1 6 8.5c-.4-.9-.3-2.5 0-3.3z" fill="#ef8f1f"/>
        </svg>
        0417 552 308
      </div>
    </div>
    <div class="back-brand">HALLORAN FIELD SERVICES</div>

    <ul class="services">
      <li><svg width="11" height="11" viewBox="0 0 11 11" aria-hidden="true"><path d="M1 10C1 4 5 1 10 1 10 6 7 10 1 10z" fill="#ef8f1f"/></svg>
        <strong>Bulk Fertilizer</strong>including Lime, Gypsum,<br>Manure &amp; Compost</li>
      <li><svg width="11" height="11" viewBox="0 0 11 11" aria-hidden="true"><path d="M1 10C1 4 5 1 10 1 10 6 7 10 1 10z" fill="#ef8f1f"/></svg>
        <strong>Granular Fertilizer</strong>including Single Super,<br>Urea, Gran-am<br>&amp; Custom Blends</li>
      <li><svg width="11" height="11" viewBox="0 0 11 11" aria-hidden="true"><path d="M1 10C1 4 5 1 10 1 10 6 7 10 1 10z" fill="#ef8f1f"/></svg>
        <strong>Modern Equipment</strong>Autosteer &amp; Variable<br>Rate Capable</li>
      <li><svg width="11" height="11" viewBox="0 0 11 11" aria-hidden="true"><path d="M1 10C1 4 5 1 10 1 10 6 7 10 1 10z" fill="#ef8f1f"/></svg>
        <strong>Friendly &amp; Reliable Service</strong></li>
    </ul>
  </section>
</body>
</html>
```